Brookvale Building Company - advertisement poster

I am looking to print some canvas signs to advertise my general contracting company, Brookvale Building Company. The sign will measure 6' long x 3' high so the size should match that ratio. I already have a logo icon, which is the Letter 'B' and some trees that I would like to incorporate, see attached. I would also like the to have the following information listed:
1) phone number: 831-555-0172
2) email: brookvalebuildingcompany@mailnest.example
3) website: brookvalebuildingcompany.example
4) Lic#4826130
5) I want to use this text: "BUILD WITH THE B-CREW!"

The ad should be relatively simple and clean. Black and Green are my company colors. I am open to creative ideas!

Target Market(s)

People looking to renovate their homes

Industry/Entity Type

Construction

Colors
59FF00
82FF00
B8FF75
E3FFCB
F4FFEA

Requirements
Must have
• Must have my company logo
Should not have
• No photos or complex graphics

```html
<!DOCTYPE html>
<html lang="en">
<head>
<meta charset="utf-8">
<title>Brookvale Building Company – Sign</title>
<link rel="stylesheet" href="https://fonts.googleapis.com/css2?family=Archivo+Black&family=Michroma&family=Montserrat:wght@800&family=Roboto+Condensed:wght@700&display=swap">
<style>
  :root {
    --ink: #1c1c1c;
    --paper: #ffffff;
    --green: #5cb83a;
    --green-bright: #59ff00;
    --muted: #6a6a6a;
    --backdrop: #e9ece6;
  }
  html, body {
    margin: 0;
    width: 1200px;
    height: 800px;
    overflow: hidden;
    background: var(--backdrop);
  }
  .sign {
    position: absolute;
    left: 20px;
    top: 110px;
    width: 1160px;
    height: 580px;
    background: var(--paper);
    overflow: hidden;
    box-shadow: 0 6px 24px rgba(0,0,0,.18);
  }
  .sign__shapes {
    position: absolute;
    inset: 0;
  }
  .license {
    position: absolute;
    left: 50px;
    top: 40px;
    font-family: "Montserrat", sans-serif;
    font-weight: 800;
    font-size: 17px;
    color: var(--muted);
    letter-spacing: .5px;
  }
  .brand {
    position: absolute;
    left: 40px;
    top: 150px;
    width: 560px;
    text-align: center;
    color: var(--paper);
    font-family: "Michroma", sans-serif;
  }
  .brand__mark {
    width: 64px;
    height: 64px;
    background: var(--green);
    margin: 0 auto 22px;
  }
  .brand__est {
    position: absolute;
    top: 40px;
    font-size: 14px;
    letter-spacing: 5px;
  }
  .brand__est--left { left: 40px; }
  .brand__est--right { right: 40px; }
  .brand__name {
    font-size: 52px;
    line-height: 1;
    letter-spacing: 2px;
  }
  .brand__sub {
    font-size: 21px;
    letter-spacing: 7px;
    margin-top: 14px;
  }
  .headline {
    position: absolute;
    left: 660px;
    top: 86px;
    width: 480px;
    text-align: center;
    line-height: 1;
  }
  .headline__build {
    font-family: "Archivo Black", sans-serif;
    font-size: 128px;
    color: var(--ink);
    letter-spacing: -2px;
  }
  .headline__with {
    font-family: "Archivo Black", sans-serif;
    font-size: 66px;
    color: var(--ink);
    margin-top: 2px;
  }
  .headline__crew {
    font-family: "Michroma", sans-serif;
    font-size: 58px;
    color: var(--green);
    margin-top: 6px;
    letter-spacing: 2px;
  }
  .phone {
    position: absolute;
    left: 50px;
    top: 396px;
    display: flex;
    align-items: center;
    gap: 20px;
    font-family: "Archivo Black", sans-serif;
    font-size: 56px;
    color: var(--ink);
    line-height: 1;
  }
  .email {
    position: absolute;
    left: 666px;
    top: 400px;
    width: 466px;
    height: 54px;
    border-radius: 27px;
    background: var(--green);
    display: flex;
    align-items: center;
    justify-content: center;
    gap: 10px;
    font-family: "Roboto Condensed", sans-serif;
    font-weight: 700;
    font-size: 18px;
    color: var(--ink);
  }
  .website {
    position: absolute;
    left: 50px;
    top: 484px;
    height: 96px;
    display: flex;
    align-items: center;
    gap: 26px;
    font-family: "Montserrat", sans-serif;
    font-weight: 800;
    font-size: 48px;
    color: var(--paper);
    letter-spacing: 1px;
  }
</style>
</head>
<body>
  <main class="sign">
    <svg class="sign__shapes" width="1160" height="580" viewBox="0 0 1160 580" aria-hidden="true">
      <polygon points="0,0 520,0 648,262 576,383 0,383" fill="var(--ink)"/>
      <polygon points="536,0 556,0 690,262 592,383 578,383 666,262" fill="var(--green)"/>
      <rect x="0" y="475" width="1160" height="105" fill="var(--ink)"/>
    </svg>

    <div class="license">License Number: 4826130</div>

    <div class="brand">
      <div class="brand__mark"></div>
      <span class="brand__est brand__est--left">ESTD</span>
      <span class="brand__est brand__est--right">2020</span>
      <div class="brand__name">BROOKVALE</div>
      <div class="brand__sub">BUILDING COMPANY</div>
    </div>

    <h1 class="headline" style="margin:0;font-weight:normal">
      <div class="headline__build">BUILD</div>
      <div class="headline__with">WITH</div>
      <div class="headline__crew">B-CREW!</div>
    </h1>

    <div class="phone">
      <svg width="64" height="60" viewBox="0 0 64 60" aria-hidden="true">
        <path d="M10 10 l10 -4 l8 14 l-7 6 c3 7 8 12 15 15 l6 -7 l14 8 l-4 10 c-22 2 -44 -20 -42 -42z" fill="var(--green)"/>
        <path d="M36 6 a18 18 0 0 1 18 18" stroke="var(--green)" stroke-width="4" fill="none" stroke-linecap="round"/>
        <path d="M38 0 a26 26 0 0 1 24 24" stroke="var(--green)" stroke-width="4" fill="none" stroke-linecap="round"/>
      </svg>
      <span>831.555.0172</span>
    </div>

    <div class="email">
      <svg width="26" height="18" viewBox="0 0 26 18" aria-hidden="true">
        <rect x="1" y="1" width="24" height="16" fill="var(--ink)"/>
        <path d="M1 1 L13 10 L25 1" stroke="var(--green)" stroke-width="2" fill="none"/>
      </svg>
      <span>BrookvaleBuildingCompany@mailnest.example</span>
    </div>

    <div class="website">
      <svg width="58" height="58" viewBox="0 0 58 58" aria-hidden="true" fill="none" stroke="var(--paper)" stroke-width="3.5">
        <circle cx="29" cy="29" r="26"/>
        <ellipse cx="29" cy="29" rx="12" ry="26"/>
        <line x1="29" y1="3" x2="29" y2="55"/>
        <line x1="3" y1="29" x2="55" y2="29"/>
        <line x1="7" y1="16" x2="51" y2="16"/>
        <line x1="7" y1="42" x2="51" y2="42"/>
      </svg>
      <span>BrookvaleBuildingCompany.example</span>
    </div>
  </main>
</body>
</html>
```